Book Cover on Entrepreneurship for Eye Doctors

Book Title: The Lens Practice Builder: How to launch with confidence
Author: Rufus Tembley, Optom, MBA, DBA, EIC
I need a Book Cover with the following descriptions:
Topic: the book topic is entrepreneurship knowledge for eye care professionals.
The book's audience: eye care professionals who you know as Opticians, who sell eyeglasses and sunglasses;
Optometrists, test eyes, fit contact lenses, and prescribe medication
Ophthalmologists, perform eye surgery
More about the audience:
1- Young eye care professionals who don’t know about entrepreneurship and those who are stuck in the 9-to-5 job;
2- This is the first book written on entrepreneurship with eye care professionals in mind.
3- Private practice owners the established business guys who are looking to grow their business;
4- Many eye care professionals are MBA holders they may have learned a little bit about entrepreneurship during their MBA studies.
Use the sample cover above and the suggestions that follow as a guide:
1- The cover should be very simple leaving an empty space somewhere to sign the book;
2- The Title and author name should use a modern font;
3- The cover should provide info about what's inside the book through illustrations, for example:
a- Gears: illustrating entrepreneur growth mindset (or anything more explicit)
b- Spectacles, sunglasses, lenses, eye drops, or any other eye care-related correction tools illustrating eye care (or anything more explicit)
c- Symbols illustrating ideas, opportunity, and profit, like money, charts, light bulbs, brain, and coins,...(or anything more explicit)
d- Entrepreneurship illustrated by Briefcase, tie, suit,... (or anything more explicit)

The rest is your creativity and imagination interplay.

Target Market(s)

Eye care professionals: Opticians, Optometrists, Ophthalmologists, Eye Care Administrators, Students in eye specialties.

Industry/Entity Type

eye care

Requirements
Must have
• 1- The cover should be very simple leaving an empty space somewhere to sign the book; 2- The Title and author name should use a modern font; 3- The cover should provide info about what's inside the book through illustrations, for example: a- Gears: illustrating entrepreneur growth mindset (or anything more explicit) b- Spectacles, sunglasses, lenses, eye drops, or any other eye care-related correction tools illustrating eye care (or anything more explicit) c- Symbols illustrating ideas, opportunity, and profit, like money, charts, light bulbs, brain, and coins,...(or anything more explicit) d- Entrepreneurship illustrated by Briefcase, tie, suit,... (or anything more explicit)

```html
<!DOCTYPE html>
<html lang="en">
<head>
<meta charset="utf-8">
<title>The Lens Practice Builder — Book Cover</title>
<link rel="stylesheet" href="https://fonts.googleapis.com/css2?family=Bebas+Neue&family=Montserrat:wght@400;700&display=swap">
<style>
  :root {
    --backdrop: #6a6a6a;
    --cover-white: #ffffff;
    --navy: #0b2340;
    --series-blue: #1d3d6f;
    --accent-cyan: #0ba9cc;
    --chart-teal: #2c9db8;
    --chart-teal-dark: #1f7f97;
    --coat-light: #e6e6ef;
    --coat-mid: #f1f1f6;
  }
  html, body {
    margin: 0;
    padding: 0;
    width: 1199px;
    height: 1200px;
    overflow: hidden;
    background: var(--backdrop);
  }
  .canvas { display: block; width: 1199px; height: 1200px; }
  .cover-sheet { fill: var(--cover-white); }
  .series-label {
    font-family: "Montserrat", sans-serif;
    font-weight: 700;
    font-size: 20px;
    letter-spacing: 1px;
    fill: var(--series-blue);
  }
  .title-main {
    font-family: "Bebas Neue", sans-serif;
    fill: var(--navy);
  }
  .title-accent {
    font-family: "Bebas Neue", sans-serif;
    font-size: 106px;
    letter-spacing: 2px;
    fill: var(--accent-cyan);
  }
  .subtitle {
    font-family: "Montserrat", sans-serif;
    font-weight: 400;
    font-size: 26px;
    letter-spacing: 1px;
    fill: var(--navy);
  }
  .growth-line {
    fill: none;
    stroke: var(--chart-teal);
    stroke-width: 30;
    stroke-linejoin: round;
    stroke-linecap: round;
  }
  .growth-head { fill: var(--chart-teal); }
  .growth-shade {
    fill: none;
    stroke: var(--chart-teal-dark);
    stroke-width: 8;
    stroke-linejoin: round;
    stroke-linecap: round;
    opacity: 0.35;
  }
  .author-band { fill: var(--accent-cyan); }
  .author-name {
    font-family: "Bebas Neue", sans-serif;
    font-size: 47px;
    fill: var(--cover-white);
  }
</style>
</head>
<body>
<svg class="canvas" viewBox="0 0 1199 1200" xmlns="http://www.w3.org/2000/svg">
  <defs>
    <linearGradient id="coatFade" x1="0" y1="0" x2="0" y2="1">
      <stop offset="0" stop-color="var(--coat-light)"/>
      <stop offset="0.7" stop-color="var(--coat-mid)"/>
      <stop offset="1" stop-color="var(--cover-white)"/>
    </linearGradient>
    <linearGradient id="coatSide" x1="0" y1="0" x2="1" y2="0">
      <stop offset="0" stop-color="#dcdce6" stop-opacity="0.6"/>
      <stop offset="0.5" stop-color="#ffffff" stop-opacity="0"/>
      <stop offset="1" stop-color="#dcdce6" stop-opacity="0.6"/>
    </linearGradient>
  </defs>

  <rect class="cover-sheet" x="278" y="118" width="643" height="964"/>

  <g role="img" aria-label="Photo of a white doctor's coat with a stethoscope">
    <rect x="278" y="118" width="643" height="460" fill="url(#coatFade)"/>
    <rect x="278" y="118" width="643" height="400" fill="url(#coatSide)"/>
  </g>

  <g class="growth-chart" role="img" aria-label="Rising line chart arrow">
    <polyline class="growth-line" points="447,524 530,378 594,444 645,390 712,462 750,352 790,240"/>
    <polyline class="growth-shade" points="447,524 530,378 594,444 645,390 712,462 750,352 790,240"/>
    <polygon class="growth-head" points="815,200 766,232 812,255"/>
  </g>

  <text class="series-label" x="759" y="172">BOOK - 2</text>

  <text class="title-main" x="335" y="700" font-size="206" textLength="523" lengthAdjust="spacingAndGlyphs">THE LENS</text>
  <text class="title-main" x="356" y="860" font-size="216" textLength="505" lengthAdjust="spacingAndGlyphs">PRACTICE</text>
  <text class="title-accent" x="609" y="946" text-anchor="middle">BUILDER</text>

  <text class="subtitle" x="599" y="999" text-anchor="middle">How to launch with confidence</text>

  <rect class="author-band" x="278" y="1026" width="643" height="56"/>
  <text class="author-name" x="599" y="1072" text-anchor="middle" textLength="550" lengthAdjust="spacingAndGlyphs">RUFUS TEMBLEY, OPTOM, MBA, DBA, EIC</text>
</svg>
</body>
</html>
```